Turm7Zwerge
Zielgruppe
Zielgruppe sind die Eltern, Lehrer, Kindergärtner, aber auch Kinder, die bereits Lesen können.
Aufgabenstellung
Ich brauche einen Flyer und ein Plakat für eine Kinderschachschule für Kinder zwischen 4 und 15 Jahren. Auf dem Flyer, den ich in A6-Format drucken möchte (beidseitig), muss ich die Info über die Kinderschachschule Turm7Zwerge (mehr Infos unter www.turm7zwerge-beispiel.ch), dh., was wir machen, Kontaktdaten, etc schreiben können. Es dient als Werbematerial zum Auslegen
Auf dem Plakat wird mehr oder weniger das Gleiche stehen, es wird jedoch als Din A4 Seite aufgehängt.
Unsere Kontaktinformation ist wie folgt:
Turm7Zwerge: Züge für Wolkenkinder
www.turm7zwerge-beispiel.ch

```html
<!DOCTYPE html>
<html lang="de">
<head>
<meta charset="utf-8">
<title>Turm7Zwerge – Flyer</title>
<link href="https://fonts.googleapis.com/css2?family=Tinos:wght@400;700&display=swap" rel="stylesheet">
<style>
  :root {
    --ink: #111111;
    --pink: #e0007a;
    --yellow: #f2c200;
    --cyan: #0aa2dc;
    --paper: #ffffff;
    --photo-warm: #8a5a3c;
    --photo-dark: #3b2a22;
  }
  html, body {
    margin: 0;
    padding: 0;
    overflow: hidden;
    background: var(--paper);
  }
  .flyer {
    position: relative;
    width: 1200px;
    height: 848px;
    overflow: hidden;
    background: var(--paper);
    font-family: "Tinos", "Times New Roman", serif;
    color: var(--ink);
    font-size: 12.6px;
    line-height: 17.6px;
  }
  .block { position: absolute; }
  .block p { margin: 0; }
  .heading {
    margin: 0 0 18px;
    font-weight: 400;
    font-size: 18px;
    line-height: 22px;
    text-decoration: underline;
    text-align: center;
  }
  .heading--pink { color: var(--pink); }
  .heading--yellow { color: var(--yellow); text-align: left; }
  .heading--cyan { color: var(--cyan); font-size: 17px; margin-bottom: 0; }

  .intro-fun { left: 50px; top: 48px; width: 356px; }
  .intro-strong { left: 50px; top: 247px; width: 356px; }
  .photo-group { left: 104px; top: 487px; width: 235px; height: 308px;
    background: linear-gradient(160deg, var(--photo-warm), var(--photo-dark)); }

  .benefits { left: 427px; top: 48px; width: 360px; }
  .benefits .heading { margin-bottom: 16px; }
  .benefits ul { margin: 0; padding-left: 26px; list-style: disc; }
  .benefits li { font-size: 13.5px; line-height: 20px; }

  .photo-match { left: 427px; top: 254px; width: 337px; height: 219px;
    background: linear-gradient(135deg, #c9b49a, #4a3a30 70%, #2a211c); }

  .smart { left: 427px; top: 483px; width: 284px; font-size: 11.6px; line-height: 17.2px; }
  .smart .heading { text-align: center; width: 380px; margin-left: -10px; margin-bottom: 14px; }
  .smart ul { margin: 12px 0 0; padding-left: 26px; list-style: square; }
  .smart li { margin-bottom: 0; }

  .brand { left: 820px; top: 50px; width: 340px; height: 220px; text-align: center; }
  .brand-mark { display: inline-block; width: 26px; height: 26px; background: var(--pink); margin-top: 62px; }
  .brand-name { display: block; font-weight: 700; font-size: 50px; color: var(--pink); line-height: 1.1; margin-top: 8px; }
  .brand-tagline { display: block; font-size: 24px; letter-spacing: 1px; margin-top: 2px; }

  .contact { left: 838px; top: 296px; width: 320px; font-size: 16px; line-height: 20.3px; }
  .contact .heading { text-align: center; width: 240px; }
  .venue { left: 838px; top: 528px; width: 306px; font-size: 13px; line-height: 20.4px; }
  .opening { left: 838px; top: 686px; width: 306px; font-size: 13px; line-height: 20.4px; }
</style>
</head>
<body>
<main class="flyer">

  <section class="block intro-fun">
    <h2 class="heading heading--pink">Schach macht Spaß!!!</h2>
    <p>Schach zieht jeden Spieler sofort in seinen Bann: Kaum ist das Schachbrett aufgebaut und der erste Zug getan, beginnt die Magie zu wirken: Vor uns liegt ein ganzer Ozean voller Abenteuer und Möglichkeiten. Wir werden zum Bauern oder zum König und schlüpfen in unsere Figuren, um Freud und Leid mit ihnen zu teilen. An Spannung schlägt Schach jedes Computerspiel! Die Phantasie wird angeregt und lässt die Kinder oft nicht mehr los.</p>
  </section>

  <section class="block intro-strong">
    <h2 class="heading heading--pink">Schach macht stark!!!</h2>
    <p>Schach ist eine Lebensschule. Schon erste Erfolge im Spiel und das Lösen von Problemen stärken das Selbstvertrauen. Hier hat Jeder die Möglichkeit, seine geistigen Fähigkeiten unter Beweis zu stellen. Das Hochgefühl eines Sieges beflügelt uns auch für andere Bereiche. Gleichzeitig lernen wir, mit Niederlagen umzugehen und Verantwortung für die eigenen Züge zu übernehmen. Ebenso respektieren wir unseren Gegner und dessen Ideen. Die Spieler tragen einen fairen sportlichen Zweikampf aus, der häufig auch über das Schach hinaus verbindet.</p>
  </section>

  <div class="block photo-group" role="img" aria-label="Foto: Kinder sitzen an einer langen Tischreihe mit Schachbrettern, ein Trainer steht dabei"></div>

  <section class="block benefits">
    <h2 class="heading heading--yellow">Wir bieten:</h2>
    <ul>
      <li>Konzentrationstraining</li>
      <li>Vertrauensaufbau</li>
      <li>Stärkung des Selbstvertrauens</li>
      <li>Persönliches Wachstum</li>
      <li>Geistige Herausforderung</li>
      <li>intellektuelle Stärkung</li>
    </ul>
  </section>

  <div class="block photo-match" role="img" aria-label="Foto: zwei Kinder spielen konzentriert eine Partie Schach"></div>

  <section class="block smart">
    <h2 class="heading heading--yellow">Schach macht schlau!!!</h2>
    <p>Die positive Wirkung von Schachtraining auf Kinder und Jugendliche ist vielfach belegt. Der signifikante Intelligenzanstieg zeigt sich in zahlreichen Studien und wird insbesondere bei folgenden Werten (auch bei anfangs unterdurchschnittlichen Schülern) sichtbar:</p>
    <ul>
      <li>bessere mathematische Fähigkeiten und räumliches Vorstellungsvermögen</li>
      <li>Verbesserung kognitiver Fähigkeiten (abstraktes, analytisches Denken)</li>
      <li>höhere sprachliche Fähigkeiten (Lese- und Sprachverständnis)</li>
      <li>erhöhtes Wahrnehmungs- und Konzentrationsvermögen</li>
      <li>stärkere Leistungsmotivation und Sozialkompetenz</li>
    </ul>
  </section>

  <header class="block brand">
    <span class="brand-mark" aria-hidden="true"></span>
    <span class="brand-name">Turm7Zwerge</span>
    <span class="brand-tagline">Züge für Wolkenkinder</span>
  </header>

  <section class="block contact">
    <h2 class="heading heading--cyan">Kontakte</h2>
    <p>Turm7Zwerge: Züge für Wolkenkinder<br>
    Nora Malvik, Vorsitzende<br>
    Lindenweg 12,<br>
    Postfach 418<br>
    CH-8700 Seewald<br>
    Tel. 079 - 000 12 34<br>
    info@turm7zwerge-beispiel.ch<br>
    www.turm7zwerge-beispiel.ch</p>
  </section>

  <section class="block venue">
    <p>Unser Hauptkurslokal befindet sich in Seewald, Uferweg 2. Sie können mit dem Zug zum Bahnhof Seewald fahren und dann den Uferweg hinauflaufen oder Sie kommen mit dem Bus 410, 412 oder 416 Haltestelle Brunnenplatz und laufen den Uferweg hinunter.</p>
  </section>

  <section class="block opening">
    <p>Unsere Schule wird im August mit den ersten Kursen starten! Wir möchten Sie jetzt schon bei uns begrüssen!</p>
  </section>

</main>
</body>
</html>
```